Harborline Lending and Capital. We provide MOSTLY residential home mortgages in Florida AND commercial loans for investment properties throughout the United states.
I would love to emulate so of the lender sites that are available on the internet but I would like to have the site as popular as possible for SEO purposes. Clients can already click the link to take them to the mortgage application where they can complete that and upload documents. If you could polish that up for me that would be great. I can also provide you with great detail on loan programs that are currently being offered. WE OFFER ALL MORTGAGE LENDING PRODUCTS. I would also like to add something in reference to the rate but I don't think it's legal to actually state or promise a rate for mortgage since they vary based on loan type, client and other criteria...

On the Harborline real estate site I would like to add a link or some way for clients to be able to put in credit card information to render services ...

Please let me know what you need from me

Thank you !!

Current link to site to improve and code

https://harborlinelendingandcapital.example/

Industry/Entity Type

Residential and commmercial lending

Coding

Coded - Design and coding required

Number of Pages Required

2 page

Requirements
Must have
• Love to integrate Mortgage interest rates even if general
Nice to have
• Link to fill out mortgage application via Quorvel LPX software

```html
<!DOCTYPE html>
<html lang="en">
<head>
<meta charset="utf-8">
<title>Harborline Lending and Capital</title>
<link href="https://fonts.googleapis.com/css2?family=Plus+Jakarta+Sans:wght@400;500;600;700;800&display=swap" rel="stylesheet">
<style>
:root{
  --forest:#1c3a1f;
  --forest-deep:#16301a;
  --lime:#8dc03f;
  --mint:#c8e4c4;
  --ink:#1d1d1d;
  --text:#3d3d3d;
  --muted:#6a6a6a;
  --card:#ffffff;
  --soft:#f7f7f1;
  --star:#f29a1d;
}
*{box-sizing:border-box;margin:0;padding:0}
html,body{width:1200px;height:4458px;overflow:hidden}
body{position:relative;background:#fff;font-family:"Plus Jakarta Sans",Arial,sans-serif;color:var(--text)}
.abs{position:absolute}
.photo{position:absolute;overflow:hidden}
.heading{position:absolute;left:0;width:1200px;text-align:center;font-weight:700;font-size:35px;color:var(--ink);letter-spacing:-.3px}
.accent{color:var(--lime);text-decoration:underline;text-decoration-color:var(--forest);text-decoration-thickness:3px;text-underline-offset:7px}
.btn{position:absolute;display:flex;align-items:center;gap:8px;padding:0 5px 0 12px;height:31px;border-radius:6px;background:var(--forest);color:#fff;font-size:11.5px;font-weight:500;text-decoration:none;border:2px solid #fff;box-shadow:0 0 0 1px var(--forest);white-space:nowrap}
.btn .arrow{width:21px;height:21px;border-radius:4px;background:#fff;display:flex;align-items:center;justify-content:center}

/* header */
.hero{left:0;top:0;width:1200px;height:635px;background:linear-gradient(180deg,#141a14 0%,#3b4a3a 18%,#6d7f6a 40%,#4f6a3c 62%,#2f4a25 100%)}
.hero-shade{position:absolute;left:0;top:0;width:1200px;height:635px;background:linear-gradient(180deg,rgba(0,0,0,.75) 0%,rgba(0,0,0,.15) 25%,rgba(0,0,0,.1) 60%,rgba(0,0,0,.35) 100%)}
.brand{position:absolute;left:142px;top:22px;display:flex;align-items:center;gap:10px;color:#fff;font-weight:700;font-size:12px;letter-spacing:.3px;text-decoration:none}
.brand-dot{width:40px;height:40px;border-radius:50%;background:#fff}
.nav{position:absolute;top:24px;left:722px;font-size:12px;color:#fff}
.nav a{color:#fff;text-decoration:none;position:absolute;white-space:nowrap;top:5px}
.nav .contact{top:0;background:var(--lime);border-radius:14px;padding:6px 0;width:88px;text-align:center;font-size:11px}
.hero-bar{left:142px;top:272px;width:5px;height:149px;background:var(--lime)}
.hero-title{left:166px;top:260px;font-size:52px;line-height:59px;font-weight:800;color:#fff;letter-spacing:-.3px;white-space:nowrap}

/* about */
.about-label{left:613px;top:728px;font-size:14px;color:var(--lime)}
.about-title{left:613px;top:752px;font-size:35px;line-height:41px;font-weight:700;color:var(--ink)}
.about-copy{left:613px;top:845px;width:430px;font-size:12.5px;line-height:22.5px;color:var(--text)}
.about-copy p+p{margin-top:6px}
.exp{left:156px;top:966px;width:175px;height:104px;background:var(--forest);border-radius:14px;color:#fff;text-align:center;padding-top:20px}
.exp b{display:block;font-size:32px;font-weight:700;line-height:36px}
.exp span{font-size:13px}

/* loans */
.loan-wash{left:0;top:1380px;width:1200px;height:320px;background:linear-gradient(180deg,#fff 0%,#cfe7f1 30%,#8cc6dd 65%,#6fb3cf 100%)}
.loan-card{position:absolute;top:1254px;width:282px;height:365px;background:var(--card);border-radius:0 0 28px 28px;box-shadow:0 6px 20px rgba(0,0,0,.06)}
.loan-card .pic{position:absolute;left:0;top:0;width:282px;height:185px}
.loan-card h3{position:absolute;left:22px;top:175px;width:238px;height:32px;background:#fff;text-align:center;font-size:18px;font-weight:600;color:var(--forest);padding-top:8px}
.loan-card p{position:absolute;left:17px;top:221px;width:252px;font-size:12.5px;line-height:21px;color:var(--text)}
.loan-card .btn{left:20px;top:327px}

/* properties */
.band{left:0;top:1700px;width:1200px;height:404px;background:var(--forest)}
.band-heading{color:#fff}
.band-copy{left:0;top:1855px;width:1200px;text-align:center;font-size:12.5px;line-height:23px;color:#fff}
.prop{position:absolute;top:1938px;width:216px;height:317px;border-radius:10px;overflow:hidden}
.prop .shade{position:absolute;left:0;top:0;width:100%;height:100%;background:linear-gradient(180deg,rgba(0,0,0,0) 45%,rgba(22,48,26,.95) 100%)}
.prop span{position:absolute;left:0;bottom:16px;width:100%;text-align:center;color:#fff;font-size:14px;font-weight:600;text-decoration:underline;text-underline-offset:3px}

/* testimonials */
.quote-card{position:absolute;top:2488px;width:282px;height:248px;background:var(--soft);border:1.5px solid #cfe1b3;border-radius:14px}
.stars{position:absolute;left:19px;top:22px;color:var(--star);font-size:13px;letter-spacing:2px}
.quote-card p{position:absolute;left:19px;top:47px;width:246px;font-size:12.5px;line-height:21.5px}
.who{position:absolute;left:19px;top:182px;display:flex;align-items:center;gap:10px;font-size:13px;color:var(--ink)}
.avatar{width:46px;height:46px;border-radius:50%;background:#d9cfc4}
.qmark{position:absolute;right:20px;top:194px}
.circle-arrow{position:absolute;top:2593px;width:36px;height:36px;border-radius:50%;display:flex;align-items:center;justify-content:center}
.dot{position:absolute;top:2760px;width:14px;height:14px;border-radius:50%;border:1.5px solid var(--lime)}

/* blogs */
.blog-card{position:absolute;top:2939px;width:282px;height:372px;background:#fff;border:1px solid #ececec;border-top:none;border-radius:0 0 28px 28px}
.blog-card .pic{position:absolute;left:-1px;top:0;width:282px;height:196px}
.date{position:absolute;left:14px;top:171px;background:#fff;padding:4px 12px 0 12px;font-size:10.5px;color:var(--text);height:25px}
.blog-card h3{position:absolute;left:17px;top:218px;width:246px;font-size:17px;font-weight:600;color:var(--ink);padding-bottom:8px;border-bottom:1px solid #ddd}
.blog-card p{position:absolute;left:17px;top:260px;width:252px;font-size:12.5px;line-height:21px}
.blog-card .btn{left:20px;top:357px}

/* contact */
.touch{left:142px;top:3498px;width:916px;height:507px;border-radius:32px;overflow:hidden}
.touch-photo{left:445px;top:0;width:471px;height:507px;background:linear-gradient(160deg,#f2f2ef 0%,#dfe2e4 45%,#3b4658 75%,#d9d4ce 100%)}
.touch-form{position:absolute;left:0;top:0;width:470px;height:507px;background:var(--mint);border-radius:32px}
.field-label{position:absolute;left:44px;font-size:12.5px;color:var(--ink)}
.field{position:absolute;left:38px;width:390px;background:#fff;border-radius:8px}
.submit{position:absolute;left:38px;top:414px;width:390px;height:41px;background:var(--forest);border-radius:6px;color:#fff;font-size:13px;font-weight:700;letter-spacing:.4px;display:flex;align-items:center;justify-content:center}

/* footer */
.footer{left:0;top:4094px;width:1200px;height:364px;background:var(--forest);color:#fff}
.foot-h{position:absolute;top:80px;font-size:14.5px;font-weight:500;letter-spacing:.3px}
.foot-h::after{content:"";position:absolute;left:0;top:26px;width:100%;height:2px;background:#a8c391}
.foot-list{position:absolute;top:126px;list-style:none;font-size:12px}
.foot-list li{display:flex;align-items:center;gap:8px;height:32px}
.ring{width:12px;height:12px;border:1px solid #fff;border-radius:50%}
.contact-list{position:absolute;left:312px;top:124px;list-style:none;font-size:12px;line-height:16px}
.contact-list li{display:flex;gap:12px;margin-bottom:18px}
.social{position:absolute;left:611px;top:124px;list-style:none;font-size:12px}
.social li{display:flex;align-items:center;gap:10px;height:39px}
.social .ring{width:24px;height:24px}
.foot-brand{position:absolute;left:776px;top:75px;display:flex;align-items:center;gap:10px;font-size:11px;font-weight:700;letter-spacing:.3px}
.foot-brand .brand-dot{width:46px;height:46px}
.foot-copy{position:absolute;left:776px;top:170px;width:283px;font-size:12px;line-height:19px}
.foot-copy a{color:#fff;text-decoration:underline}
.foot-bottom{position:absolute;left:0;top:316px;width:1200px;border-top:1px solid rgba(255,255,255,.35);font-size:11.5px}
.foot-bottom span{position:absolute;top:18px}
</style>
</head>
<body>

<!-- Header / hero -->
<header class="abs hero" role="img" aria-label="Aerial view of a riverside city with green parkland"></header>
<div class="hero-shade"></div>
<a class="brand" href="#">
  <span class="brand-dot"></span>
  <span>HARBORLINE LENDING AND CAPITAL</span>
</a>
<nav class="nav">
  <a href="#" style="left:0">Home</a>
  <a href="#" style="left:73px">About Us</a>
  <a href="#" style="left:161px">Properties</a>
  <a href="#" class="contact" style="left:248px">Contact Us</a>
</nav>
<div class="abs hero-bar"></div>
<h1 class="abs hero-title">Empowering<br>Homeownership,<br>Securing Investments</h1>

<!-- About -->
<div class="photo" style="left:142px;top:703px;width:310px;height:246px;border-radius:18px 18px 0 18px;background:linear-gradient(135deg,#dfe4e6 0%,#9aa4a8 40%,#4b5358 70%,#cdbfae 100%)" role="img" aria-label="Advisors reviewing loan documents with clients at a table"></div>
<div class="photo" style="left:348px;top:878px;width:222px;height:206px;border-radius:0 0 18px 0;border:4px solid #fff;background:linear-gradient(160deg,#5e93c9 0%,#9cc0dc 35%,#e6c17a 60%,#7e8b86 100%)" role="img" aria-label="Modern glass office building"></div>
<div class="abs exp"><b>25+</b><span>Years of Experience</span></div>
<div class="abs about-label">About</div>
<h2 class="abs about-title">Harborline Lending and<br><span class="accent">Capital</span></h2>
<div class="abs about-copy">
  <p>Harborline Originates Residential Home loans in Florida and Commercial and business financing in all 50 States.</p>
  <p>We have over 25 years of experience in ALL types of real estate and commercial lending. We are strategically partnered to help you obtain ALL necessary components of residential and commercial lending. From the RIGHT lending partners to the best practice Insurance avenues and commercial and residential real estate partners</p>
</div>
<a class="btn" href="#" style="left:613px;top:1027px">Read More <span class="arrow"><svg width="11" height="11" viewBox="0 0 11 11"><path d="M2 9L9 2M4 2h5v5" stroke="#1c3a1f" stroke-width="1.4" fill="none"/></svg></span></a>

<!-- Types of loans: general rate guidance and application -->
<h2 class="heading" style="top:1168px">Types of <span class="accent">Loans</span></h2>
<div class="abs loan-wash" role="img" aria-label="Resort pool water with sunlit deck"></div>

<article class="loan-card" style="left:142px">
  <div class="photo pic" style="background:linear-gradient(150deg,#ece8e2 0%,#c9b8a6 45%,#7a6a5a 80%,#b79a6a 100%)" role="img" aria-label="Hands holding a small model house over coins"></div>
  <h3>Residential Loans</h3>
  <p>General rates for 30 and 15 year fixed, ARM, FHA and VA home loans in Florida. Rates vary by loan type, credit profile and other criteria.</p>
  <a class="btn" href="https://harborlinelendingandcapital.example/rates">View Rates <span class="arrow"><svg width="11" height="11" viewBox="0 0 11 11"><path d="M2 9L9 2M4 2h5v5" stroke="#1c3a1f" stroke-width="1.4" fill="none"/></svg></span></a>
</article>
<article class="loan-card" style="left:459px">
  <div class="photo pic" style="background:linear-gradient(150deg,#a9b1b4 0%,#d8d9d6 40%,#eeeeec 65%,#9da2a0 100%)" role="img" aria-label="Cash being handed across a desk beside a laptop"></div>
  <h3>Commercial Loans</h3>
  <p>General rates for investment, multifamily and mixed-use property loans across the United States. Final terms depend on the deal and borrower.</p>
  <a class="btn" href="https://harborlinelendingandcapital.example/rates">View Rates <span class="arrow"><svg width="11" height="11" viewBox="0 0 11 11"><path d="M2 9L9 2M4 2h5v5" stroke="#1c3a1f" stroke-width="1.4" fill="none"/></svg></span></a>
</article>
<article class="loan-card" style="left:776px">
  <div class="photo pic" style="background:linear-gradient(150deg,#5a3d2a 0%,#8a6446 40%,#d9d6cf 65%,#6b4b33 100%)" role="img" aria-label="Loan agreement papers with a calculator on a wooden desk"></div>
  <h3>Other Loans</h3>
  <p>Bridge, construction, refinance and business loans. Start your mortgage application online with Quorvel LPX and upload documents securely.</p>
  <a class="btn" href="https://harborlinelendingandcapital.example/apply">Apply Now <span class="arrow"><svg width="11" height="11" viewBox="0 0 11 11"><path d="M2 9L9 2M4 2h5v5" stroke="#1c3a1f" stroke-width="1.4" fill="none"/></svg></span></a>
</article>

<!-- Available properties -->
<section class="abs band"></section>
<h2 class="heading band-heading" style="top:1792px">Available <span class="accent" style="text-decoration-color:#fff">Properties</span></h2>
<p class="abs band-copy">Lorem ipsum dolor sit amet, consectetuer adipiscing elit, sed diam nonummy nibh euismod tincidunt ut<br>laoreet dolore magna aliquam erat volutpat. Ut wisi enim ad minim veniam.</p>

<div class="prop" style="left:142px;background:linear-gradient(180deg,#dfe3e4 0%,#bfc4c3 50%,#6d716d 100%)" role="img" aria-label="White modern residence with balconies"><div class="shade"></div><span>12 Sunset Street</span></div>
<div class="prop" style="left:374px;background:linear-gradient(180deg,#7aa0c4 0%,#273341 40%,#1a2029 70%,#8a6a34 100%)" role="img" aria-label="Dark modern house lit at dusk"><div class="shade"></div><span>34 Union Avenue</span></div>
<div class="prop" style="left:608px;background:linear-gradient(180deg,#6f9bc5 0%,#b9cde0 35%,#cfcfcb 60%,#5e5b52 100%)" role="img" aria-label="Contemporary building with a perforated facade"><div class="shade"></div><span>56 Washington Street</span></div>
<div class="prop" style="left:842px;background:linear-gradient(120deg,#8b4a3c 0%,#a35b48 40%,#6f7f8e 70%,#8fb3d3 100%)" role="img" aria-label="Modern house with red timber cladding"><div class="shade"></div><span>78 Oak Boulevard</span></div>

<a class="btn" href="#" style="left:542px;top:2293px">View More <span class="arrow"><svg width="11" height="11" viewBox="0 0 11 11"><path d="M2 9L9 2M4 2h5v5" stroke="#1c3a1f" stroke-width="1.4" fill="none"/></svg></span></a>

<!-- Testimonials -->
<h2 class="heading" style="top:2407px">Client <span class="accent">Testimonials</span></h2>
<div class="circle-arrow" style="left:89px;background:#e6e6e6"><svg width="10" height="10" viewBox="0 0 10 10"><path d="M6.5 1.5L3 5l3.5 3.5" stroke="#333" stroke-width="1.5" fill="none"/></svg></div>
<div class="circle-arrow" style="left:1073px;background:var(--forest)"><svg width="10" height="10" viewBox="0 0 10 10"><path d="M3.5 1.5L7 5 3.5 8.5" stroke="#fff" stroke-width="1.5" fill="none"/></svg></div>

<article class="quote-card" style="left:142px">
  <div class="stars">★★★★★</div>
  <p>Lorem ipsum dolor sitted for going to these ametted arett consectetuer ares adiping elitted thet, sedde diam staing nonummy nibh euismod arein. Lorem Ipsum has been the industry.</p>
  <div class="who"><span class="avatar"></span>Dorian Pell</div>
  <svg class="qmark" width="38" height="26" viewBox="0 0 38 26"><path d="M8 2a6 6 0 1 0 6 6c0 7-4 13-10 16M26 2a6 6 0 1 0 6 6c0 7-4 13-10 16" stroke="#9a9a9a" stroke-width="1.3" fill="none"/></svg>
</article>
<article class="quote-card" style="left:459px">
  <div class="stars">★★★★★</div>
  <p>Lorem ipsum dolor sitted for going to these ametted arett consectetuer ares adiping elitted thet, sedde diam staing nonummy nibh euismod arein. Lorem Ipsum has been the industry.</p>
  <div class="who"><span class="avatar" style="background:#c9b3a0"></span>Lena Vasko</div>
  <svg class="qmark" width="38" height="26" viewBox="0 0 38 26"><path d="M8 2a6 6 0 1 0 6 6c0 7-4 13-10 16M26 2a6 6 0 1 0 6 6c0 7-4 13-10 16" stroke="#9a9a9a" stroke-width="1.3" fill="none"/></svg>
</article>
<article class="quote-card" style="left:776px">
  <div class="stars">★★★★★</div>
  <p>Lorem ipsum dolor sitted for going to these ametted arett consectetuer ares adiping elitted thet, sedde diam staing nonummy nibh euismod arein. Lorem Ipsum has been the industry.</p>
  <div class="who"><span class="avatar" style="background:#b9a595"></span>Owen Marsh</div>
  <svg class="qmark" width="38" height="26" viewBox="0 0 38 26"><path d="M8 2a6 6 0 1 0 6 6c0 7-4 13-10 16M26 2a6 6 0 1 0 6 6c0 7-4 13-10 16" stroke="#9a9a9a" stroke-width="1.3" fill="none"/></svg>
</article>
<span class="dot" style="left:563px"></span>
<span class="dot" style="left:592px;background:var(--forest);box-shadow:inset 0 0 0 2px #fff"></span>
<span class="dot" style="left:622px"></span>

<!-- Blogs -->
<h2 class="heading" style="top:2851px">Our Latest <span class="accent">Blogs</span></h2>

<article class="blog-card" style="left:142px">
  <div class="photo pic" style="background:linear-gradient(150deg,#f1f1ef 0%,#d8d4cf 40%,#3c3d41 70%,#e5e3df 100%)" role="img" aria-label="Professionals meeting around an office table"></div>
  <div class="date">Nov 14, 2024</div>
  <h3>Title will come here...</h3>
  <p>Lorem ipsum dolor sitted isnot for amet, consectetuer adipiscing elit, sedd diam nonummy nibh euismod tincidunt utted laoreet dolore magna aliquam.</p>
  <a class="btn" href="#">Read More <span class="arrow"><svg width="11" height="11" viewBox="0 0 11 11"><path d="M2 9L9 2M4 2h5v5" stroke="#1c3a1f" stroke-width="1.4" fill="none"/></svg></span></a>
</article>
<article class="blog-card" style="left:459px">
  <div class="photo pic" style="background:linear-gradient(180deg,#b8c7d6 0%,#e4e6e4 40%,#5b6a4a 75%,#b3b0a6 100%)" role="img" aria-label="White family house with a long driveway"></div>
  <div class="date">Nov 14, 2024</div>
  <h3>Title will come here...</h3>
  <p>Lorem ipsum dolor sitted isnot for amet, consectetuer adipiscing elit, sedd diam nonummy nibh euismod tincidunt utted laoreet dolore magna aliquam.</p>
  <a class="btn" href="#">Read More <span class="arrow"><svg width="11" height="11" viewBox="0 0 11 11"><path d="M2 9L9 2M4 2h5v5" stroke="#1c3a1f" stroke-width="1.4" fill="none"/></svg></span></a>
</article>
<article class="blog-card" style="left:776px">
  <div class="photo pic" style="background:linear-gradient(160deg,#9aa0a0 0%,#cfd0cc 40%,#6f8fa3 70%,#d7d3c9 100%)" role="img" aria-label="Family relaxing together in front of their new home"></div>
  <div class="date">Nov 14, 2024</div>
  <h3>Title will come here...</h3>
  <p>Lorem ipsum dolor sitted isnot for amet, consectetuer adipiscing elit, sedd diam nonummy nibh euismod tincidunt utted laoreet dolore magna aliquam.</p>
  <a class="btn" href="#">Read More <span class="arrow"><svg width="11" height="11" viewBox="0 0 11 11"><path d="M2 9L9 2M4 2h5v5" stroke="#1c3a1f" stroke-width="1.4" fill="none"/></svg></span></a>
</article>

<!-- Contact -->
<h2 class="heading" style="top:3414px">Get in <span class="accent">Touch</span></h2>
<section class="abs touch">
  <div class="photo touch-photo" role="img" aria-label="Advisor explaining a document to a client"></div>
  <form class="touch-form">
    <label class="field-label" style="top:50px">Name*</label>
    <div class="field" style="top:73px;height:41px"></div>
    <label class="field-label" style="top:130px">Email*</label>
    <div class="field" style="top:152px;height:42px"></div>
    <label class="field-label" style="top:210px">Phone*</label>
    <div class="field" style="top:232px;height:41px"></div>
    <label class="field-label" style="top:291px">Your Message*</label>
    <div class="field" style="top:312px;height:84px"></div>
    <div class="submit">SUBMIT NOW</div>
  </form>
</section>

<!-- Footer -->
<footer class="abs footer">
  <div class="foot-h" style="left:142px">QUICK LINKS</div>
  <ul class="foot-list" style="left:142px">
    <li><span class="ring"></span>Home</li>
    <li><span class="ring"></span>About Us</li>
    <li><span class="ring"></span>Properties</li>
    <li><span class="ring"></span>Contact Us</li>
  </ul>
  <div class="foot-h" style="left:312px">CONTACT DETAILS</div>
  <ul class="contact-list">
    <li><svg width="12" height="14" viewBox="0 0 12 14"><path d="M6 13S1 8 1 5a5 5 0 0 1 10 0c0 3-5 8-5 8z" fill="#fff"/><circle cx="6" cy="5" r="1.8" fill="#1c3a1f"/></svg><span>Seabreeze Plaza Suite 0152<br>Harbor Point FL Home.</span></li>
    <li><svg width="12" height="12" viewBox="0 0 12 12"><path d="M2.5 1h2l1 3-1.5 1a7 7 0 0 0 3 3l1-1.5 3 1v2a1 1 0 0 1-1 1A10 10 0 0 1 1.5 2a1 1 0 0 1 1-1z" fill="#fff"/></svg><span>(555) 014-2290</span></li>
    <li><svg width="13" height="10" viewBox="0 0 13 10"><rect x=".5" y=".5" width="12" height="9" rx="1" fill="#fff"/><path d="M1 1l5.5 4.5L12 1" stroke="#1c3a1f" fill="none"/></svg><span>info@harborlinelending.example</span></li>
  </ul>
  <div class="foot-h" style="left:611px">FOLLOW US</div>
  <ul class="social">
    <li><span class="ring"></span>Community</li>
    <li><span class="ring"></span>Gallery</li>
    <li><span class="ring"></span>Video Channel</li>
  </ul>
  <div class="foot-brand"><span class="brand-dot"></span><span>HARBORLINE LENDING AND CAPITAL</span></div>
  <p class="foot-copy">Lorem ipsum dolor sitte tincidunt utmost laoreet amet, consectet ueri adipiscing elit, sedden diam nonummy nibh euismod tincidunt utmost are inn laoreet dolore mere ot app lok. <a href="#">Read More</a></p>
  <div class="foot-bottom">
    <span style="left:142px">© 2025 Harborline Lending and Capital. All Rights Reserved.</span>
    <span style="left:841px">Privacy Policy</span>
    <span style="left:938px">|</span>
    <span style="left:962px">Terms of Service</span>
  </div>
</footer>

</body>
</html>
```